Quorva - corporate Business Card

We need a good look and innovative business card for a new start up company based in Los Angeles called "Quorva". We are in a payment business, including payment card, app, and ewallet. We are expert in online payment and Card not present (CNP) transaction.
We need an innovative, modern business card.

Our logo font is Aero Matics

Target Market(s)

Startup - Bank - Online Payment - Card Manufacturing

Industry/Entity Type

Startup

Contact Information for Business Card

phone: 555 014 7396 - Address: 4172 Marlowe blvd, Brenton Heights, OR 90299

Requirements
Must have
• Message: innovative, professional, expert, high tech, trust, online payment expert, security
Nice to have
• no comment
Should not have
• no Comment

```html
<!DOCTYPE html>
<html lang="en">
<head>
<meta charset="utf-8">
<title>Quorva — Business Card</title>
<link href="https://fonts.googleapis.com/css2?family=Roboto:wght@300;400;500&display=swap" rel="stylesheet">
<style>
  :root {
    --brand-red: #b81f30;
    --ink: #4a4a4a;
    --muted: #8a8a8a;
    --rule: #b5b5b5;
    --paper: #ffffff;
    --backdrop: #2b2b2b;
  }
  * { box-sizing: border-box; margin: 0; padding: 0; }
  html, body {
    width: 1200px; height: 950px; overflow: hidden;
    background: var(--backdrop);
    font-family: "Roboto", Arial, sans-serif;
  }
  .sheet {
    width: 1200px; height: 950px;
    display: flex; flex-direction: column; align-items: center; justify-content: center;
    gap: 50px;
  }
  .card {
    position: relative;
    width: 700px; height: 400px;
    border-radius: 4px;
    overflow: hidden;
  }
  /* Front */
  .card-front { background: var(--paper); }
  .card-front .brand {
    position: absolute; left: 60px; top: 70px;
    display: flex; align-items: center; gap: 10px;
  }
  .brand-dot {
    width: 62px; height: 62px; border-radius: 50%;
    background: var(--brand-red);
  }
  .card-front .brand-name {
    font-weight: 500; font-size: 50px; color: var(--brand-red);
    letter-spacing: 0.5px; line-height: 1;
  }
  .address {
    position: absolute; right: 48px; top: 182px;
    text-align: right; font-size: 15px; font-weight: 400;
    color: var(--ink); line-height: 1.4;
  }
  .divider {
    position: absolute; left: 150px; right: 48px; top: 240px;
    height: 1px; background: var(--rule);
  }
  .person {
    position: absolute; left: 60px; top: 200px;
  }
  .person-name {
    font-size: 20px; font-weight: 400; color: var(--brand-red);
  }
  .person-title {
    font-size: 15px; font-weight: 300; color: var(--muted); margin-top: 2px;
  }
  .contacts {
    position: absolute; left: 60px; top: 262px;
    list-style: none; font-size: 14px; color: var(--ink);
  }
  .contacts li {
    display: flex; align-items: center; gap: 10px; height: 24px;
  }
  .contacts svg { width: 14px; height: 14px; fill: var(--brand-red); }
  /* Back */
  .card-back { background: var(--brand-red); }
  .card-back .brand {
    position: absolute; left: 150px; top: 140px;
    display: flex; align-items: center; gap: 16px;
  }
  .card-back .brand-dot {
    width: 110px; height: 110px; background: var(--paper);
  }
  .card-back .brand-name {
    font-weight: 500; font-size: 92px; color: var(--paper); line-height: 1;
  }
  .web {
    position: absolute; left: 155px; top: 290px;
    font-size: 13px; font-weight: 300; color: var(--paper);
    letter-spacing: 7px;
  }
</style>
</head>
<body>
<main class="sheet">
  <section class="card card-front" aria-label="Business card front">
    <div class="brand">
      <span class="brand-dot"></span>
      <span class="brand-name">quorva</span>
    </div>
    <p class="address">4172 Marlowe blvd<br>Brenton Heights, OR 90299</p>
    <div class="person">
      <p class="person-name">Dana Ruiz</p>
      <p class="person-title">President</p>
    </div>
    <div class="divider"></div>
    <ul class="contacts">
      <li>
        <svg viewBox="0 0 16 16" aria-hidden="true"><path d="M3 1h3l1.5 4-2 1.3a8 8 0 0 0 4.2 4.2L11 8.5l4 1.5v3a2 2 0 0 1-2 2A12 12 0 0 1 1 3a2 2 0 0 1 2-2z"/></svg>
        555 014 7396
      </li>
      <li>
        <svg viewBox="0 0 16 16" aria-hidden="true"><path d="M1 3h14v10H1z"/><path d="M1.5 3.5l6.5 5.5 6.5-5.5" fill="none" stroke="#ffffff" stroke-width="1.3"/></svg>
        dana@quorva.com
      </li>
      <li>
        <svg viewBox="0 0 16 16" aria-hidden="true"><circle cx="8" cy="8" r="7"/></svg>
        www.quorva.com
      </li>
    </ul>
  </section>

  <section class="card card-back" aria-label="Business card back">
    <div class="brand">
      <span class="brand-dot"></span>
      <span class="brand-name">quorva</span>
    </div>
    <p class="web">www.quorva.com</p>
  </section>
</main>
</body>
</html>
```